Seeking a new website design for electrical contracting company

Brisket & Vane electrical contracting needs a new website for brisket-vane.example

We are looking for modern and something real cool with motion for a landing page. we have some cool images from our photo shoot. maybe even 3d motion our existing logo. we would like something we can edit with news and events and update a past project page. Also allow to take payment
stock images at
https://lorapellwinphotos.picvault-demo.example/Brisket-and-Vane

Target Market(s)

construction , home owners , business owners,

Industry/Entity Type

construction , electrical

Coding

Number of Pages Required

5+ page

Font styles to use
Serif
Sans Serif

Colors
0054AA
0677BA
7BADD7
CADEEF
E8F1F8
0094D4
00A9DD
6FCCEA
C7EBF8
E9F6FB
FFF300
FFF600
FEFA6F
FFFEC7
FFFEE8

Requirements
Must have
• excitement, motion, selling professionalism,

```html
<!DOCTYPE html>
<html lang="en">
<head>
<meta charset="utf-8">
<title>Brisket &amp; Vane Electrical Contracting</title>
<link rel="stylesheet" href="https://fonts.googleapis.com/css2?family=Poppins:wght@400;500;600;700;800&display=swap">
<style>
:root{
  --orange:#f39a1e;
  --orange-deep:#e9860a;
  --navy:#1d2a5e;
  --navy-dark:#16214b;
  --ink:#1e1e1e;
  --muted:#6b6b6b;
  --light:#f4f4f4;
  --footer:#2b2b2b;
  --white:#ffffff;
}
*{box-sizing:border-box;margin:0;padding:0}
html,body{width:1200px;height:4052px;overflow:hidden}
body{font-family:"Poppins",sans-serif;color:var(--ink);background:var(--white);position:relative}
section,header,footer{position:absolute;left:0;width:1200px}
.label{color:var(--orange);font-size:13px;font-weight:600;letter-spacing:1px;text-transform:uppercase}
.title{font-weight:800;text-transform:uppercase;color:var(--ink)}
.btn{display:inline-block;font-size:14px;font-weight:600;padding:12px 24px;border-radius:3px;color:var(--white);background:var(--navy)}
.btn-orange{background:var(--orange)}
p{font-size:14px;line-height:1.7;color:var(--muted)}

/* header */
.site-header{top:0;height:84px;z-index:5;background:rgba(255,255,255,.96)}
.brand{position:absolute;left:110px;top:22px;display:flex;align-items:center;gap:10px;font-weight:700;font-size:20px;color:var(--navy);text-transform:uppercase}
.brand-mark{width:36px;height:36px;background:var(--navy);border-radius:4px}
.nav{position:absolute;left:400px;top:28px;display:flex;gap:38px;font-size:15px;font-weight:500}
.nav .active{color:var(--orange)}
.cta-call{position:absolute;right:120px;top:20px;padding:10px 18px;font-size:14px}

/* hero */
.hero{top:0;height:684px;background:linear-gradient(110deg,#3b3f46 0%,#6d6f73 45%,#9b8f7a 100%)}
.hero-photo{position:absolute;inset:0;background:linear-gradient(90deg,rgba(20,22,28,.65) 0%,rgba(20,22,28,.15) 60%,rgba(0,0,0,0) 100%)}
.hero-copy{position:absolute;left:140px;top:230px;width:520px;color:var(--white)}
.hero-copy h1{font-size:44px;line-height:1.2;font-weight:800;text-transform:uppercase;color:var(--white)}
.hero-copy p{color:#e6e6e6;margin:16px 0 30px;font-size:16px}

/* stats */
.stats{top:684px;height:140px;display:flex;justify-content:center;gap:120px;align-items:center;border-bottom:1px solid #eee}
.stat{display:flex;align-items:center;gap:16px}
.stat svg{width:64px;height:64px}
.stat strong{display:block;font-size:42px;font-weight:700;color:var(--orange);line-height:1}
.stat span{font-size:13px;font-weight:600;color:var(--muted);text-transform:uppercase}

/* about */
.about{top:824px;height:680px;background:linear-gradient(160deg,#fff 55%,#f5f5f5 55%)}
.about .label{position:absolute;top:80px;width:100%;text-align:center}
.about .title{position:absolute;top:100px;width:100%;text-align:center;font-size:38px}
.about .lead{position:absolute;top:160px;left:300px;width:600px;text-align:center}
.about .body{position:absolute;left:148px;top:230px;width:420px}
.about .btn{position:absolute;left:148px;top:430px}
.about-photo{position:absolute;left:760px;top:236px;width:340px;height:360px;background:linear-gradient(135deg,#c9cdd3,#8b96a6);clip-path:polygon(25% 0,75% 0,100% 50%,75% 100%,25% 100%,0 50%)}
.about-badge{position:absolute;left:990px;top:480px;width:120px;height:120px;background:var(--navy);border:6px solid #fff}

/* services */
.services{top:1500px;height:620px;background:var(--orange)}
.services .label{position:absolute;top:66px;width:100%;text-align:center;color:#fff}
.services .title{position:absolute;top:88px;width:100%;text-align:center;font-size:40px;color:#fff}
.services .lead{position:absolute;top:144px;left:300px;width:600px;text-align:center;color:#fff}
.cards{position:absolute;top:232px;left:148px;display:flex;gap:8px}
.card{position:relative;width:298px;height:326px;border-radius:4px;overflow:hidden}
.card-photo{position:absolute;inset:0}
.card h3{position:absolute;left:0;right:0;bottom:18px;text-align:center;color:#fff;font-size:18px;font-weight:500}
.card-feature{background:var(--navy);text-align:center;color:#fff;padding:40px 22px}
.card-feature svg{width:56px;height:56px}
.card-feature h3{position:static;margin:22px 0 12px}
.card-feature p{color:#cfd3e0;font-size:13px}
.card-feature .more{display:inline-flex;align-items:center;gap:10px;margin-top:18px;font-size:14px;font-weight:600}
.card-feature .more i{width:28px;height:28px;background:var(--orange);display:inline-block}
.arrow{position:absolute;top:372px;width:30px;height:30px}

/* projects */
.projects{top:2200px;height:540px}
.projects .label{position:absolute;left:140px;top:68px}
.projects .title{position:absolute;left:140px;top:90px;font-size:40px}
.projects .lead{position:absolute;left:140px;top:148px;width:420px;color:var(--ink);font-size:15px}
.projects .body{position:absolute;left:140px;top:218px;width:420px}
.projects .btn{position:absolute;left:140px;top:340px}
.pager{position:absolute;left:336px;top:340px;display:flex;gap:12px}
.pager span{width:40px;height:40px;border-radius:50%;border:1px solid #ddd;display:flex;align-items:center;justify-content:center}
.pager .on{background:var(--navy);border-color:var(--navy)}
.project-photos{position:absolute;left:624px;top:30px;display:flex;gap:14px}
.project-photos div{width:190px;height:480px;border-radius:16px}

/* testimonials */
.testimonials{top:2740px;height:460px}
.testimonials .label{position:absolute;top:0;width:100%;text-align:center}
.testimonials .title{position:absolute;top:22px;width:100%;text-align:center;font-size:40px}
.avatar{position:absolute;border-radius:50%;background:linear-gradient(135deg,#d8c7b6,#8f7e6e);border:4px solid #fff;box-shadow:0 2px 8px rgba(0,0,0,.15)}
.quote{position:absolute;left:300px;top:238px;width:600px;text-align:center}
.client{position:absolute;top:344px;width:100%;text-align:center;font-weight:600;font-size:18px}
.client small{display:block;font-weight:400;font-size:12px;color:var(--muted)}
.dots{position:absolute;top:412px;left:550px;display:flex;gap:8px}
.dots i{width:22px;height:5px;background:#ddd;display:block;border-radius:3px}
.dots i.on{background:var(--navy)}

/* contact */
.contact{top:3232px;height:508px;background:var(--navy)}
.contact-photo{position:absolute;left:0;top:-110px;width:450px;height:618px;background:linear-gradient(160deg,#e8c66d 0%,#c9a35a 30%,#6f6a62 100%);clip-path:polygon(0 0,70% 0,100% 100%,0 100%)}
.contact .label{position:absolute;left:492px;top:60px}
.contact .title{position:absolute;left:492px;top:82px;font-size:40px;color:#fff}
.form{position:absolute;left:492px;top:160px;width:570px}
.field-row{display:flex;gap:30px;margin-bottom:30px}
.field{flex:1;border-bottom:1px solid rgba(255,255,255,.4);color:#cdd2e2;font-size:12px;padding-bottom:10px}
.field.tall{height:90px}
.form .btn{background:#fff;color:var(--navy)}

/* footer */
.site-footer{top:3740px;height:312px;background:var(--footer);color:#ddd}
.foot-brand{position:absolute;left:150px;top:60px;text-align:center;width:150px}
.foot-brand i{display:block;width:44px;height:44px;margin:0 auto 12px;background:#fff;border-radius:4px}
.foot-brand b{font-size:18px;text-transform:uppercase;color:#fff}
.socials{display:flex;justify-content:center;gap:10px;margin-top:14px}
.socials span{width:24px;height:24px;border-radius:50%;background:#fff}
.col{position:absolute;top:40px;font-size:13px;line-height:1.9}
.col h4{font-size:14px;font-weight:600;color:#fff;text-transform:uppercase;margin-bottom:6px}
.subscribe{position:absolute;left:796px;top:40px;width:300px}
.subscribe h4{font-size:14px;font-weight:600;color:#fff;text-transform:uppercase}
.sub-box{display:flex;margin:14px 0 16px}
.sub-box span{flex:1;height:36px;background:#444;font-size:12px;color:#aaa;padding:9px 10px}
.sub-box b{width:70px;background:var(--orange)}
.contact-line{font-size:13px;margin-bottom:8px;display:flex;gap:8px;align-items:center}
.contact-line i{width:10px;height:10px;background:var(--orange);display:inline-block}
.copyright{position:absolute;left:0;right:0;bottom:22px;text-align:center;font-size:12px;color:#aaa;border-top:1px solid #3d3d3d;padding-top:16px}
.to-top{position:absolute;right:92px;bottom:70px;width:32px;height:32px;border-radius:50%;background:var(--orange)}
</style>
</head>
<body>

<header class="site-header">
  <div class="brand"><span class="brand-mark"></span>Brisket &amp; Vane</div>
  <nav class="nav"><span class="active">Home</span><span>About Us</span><span>Services</span><span>Projects</span><span>Contact</span></nav>
  <span class="btn cta-call">Schedule a Call</span>
</header>

<section class="hero">
  <div class="hero-photo" role="img" aria-label="Electrician in a hard hat working on a laptop beside switchgear panels"></div>
  <div class="hero-copy">
    <h1>Brisket &amp; Vane<br>Electrical Contracting</h1>
    <p>Lorem ipsum dolor sit amet, consectetur adipiscing elit,sed do eiusmod tempor incididunt</p>
    <span class="btn">Get Started</span>
  </div>
</section>

<section class="stats">
  <div class="stat">
    <svg viewBox="0 0 64 64" fill="none" stroke="#1d2a5e" stroke-width="2.5"><path d="M6 34l12-12 10 6 8-4 22 12-12 10-8-6-6 6-12-10z"/><path d="M18 22l-6 14M46 22l6 14"/></svg>
    <div><strong>+2k</strong><span>Happy Clients</span></div>
  </div>
  <div class="stat">
    <svg viewBox="0 0 64 64" fill="none" stroke="#1d2a5e" stroke-width="2.5"><circle cx="32" cy="28" r="14"/><circle cx="32" cy="28" r="5"/><path d="M12 54c4-8 12-10 20-10s16 2 20 10"/></svg>
    <div><strong>+2500</strong><span>Completed Projects</span></div>
  </div>
  <div class="stat">
    <svg viewBox="0 0 64 64" fill="none" stroke="#1d2a5e" stroke-width="2.5"><path d="M20 56V30l8-18c4 0 6 4 4 10l-2 8h16c4 0 6 4 4 8l-6 18H20z"/><path d="M8 30h12v26H8z"/></svg>
    <div><strong>100%</strong><span>Success</span></div>
  </div>
</section>

<section class="about">
  <div class="label">About Us</div>
  <h2 class="title">Brisket &amp; Vane Electrical Contracting</h2>
  <p class="lead">Duis aute irure dolor in reprehenderit in voluptate velit esse cillum dolore eu fugiat nulla pariatur. Excepteur sint occaecat cupidatat non proident.</p>
  <p class="body">Lorem ipsum dolor sit amet, consectetur adipiscing elit, sed do eiusmod tempor incididunt ut labore et dolore magna aliqua. Ut enim ad minim veniam, quis nostrud exercitation ullamco laboris nisi ut aliquip ex ea commodo consequat. Duis aute irure dolor in reprehenderit in voluptate velit esse cillum dolore eu fugiat nulla pariatur.</p>
  <span class="btn">Learn More</span>
  <div class="about-photo" role="img" aria-label="Technician servicing an open electrical cabinet"></div>
  <div class="about-badge"></div>
</section>

<section class="services">
  <div class="label">What We Do</div>
  <h2 class="title">Our Services</h2>
  <p class="lead">Duis aute irure dolor in reprehenderit in voluptate velit esse cillum dolore eu fugiat nulla pariatur. Excepteur sint occaecat cupidatat non proident.</p>
  <svg class="arrow" style="left:98px" viewBox="0 0 30 30"><path d="M19 7l-8 8 8 8" fill="none" stroke="#fff" stroke-width="3"/></svg>
  <div class="cards">
    <div class="card">
      <div class="card-photo" role="img" aria-label="Electrician upgrading wiring on a ceiling" style="background:linear-gradient(160deg,#c89c55,#5a4a3a)"></div>
      <h3>Energy Upgrades</h3>
    </div>
    <div class="card card-feature">
      <svg viewBox="0 0 56 56" fill="none" stroke="#f39a1e" stroke-width="2.5"><circle cx="28" cy="28" r="24"/><path d="M31 12l-11 18h9l-3 14 11-19h-9z"/></svg>
      <h3>Electrical Construction</h3>
      <p>Lorem ipsum dolor sit amet, consectetur adipiscing elit, sed do eiusmod tempor incididunt ut labore et dolore magna aliqua. Ut enim ad minim.</p>
      <span class="more">Learn More <i></i></span>
    </div>
    <div class="card">
      <div class="card-photo" role="img" aria-label="Rows of solar panels on a roof under a blue sky" style="background:linear-gradient(180deg,#7fa7c9,#2e3c55)"></div>
      <h3>Renewable Energy</h3>
    </div>
  </div>
  <svg class="arrow" style="left:1072px" viewBox="0 0 30 30"><path d="M11 7l8 8-8 8" fill="none" stroke="#fff" stroke-width="3"/></svg>
</section>

<section class="projects">
  <div class="label">Works</div>
  <h2 class="title">Our Projects</h2>
  <p class="lead">Duis aute irure dolor in reprehenderit in voluptate velit esse cillum dolore eu fugiat.</p>
  <p class="body">Lorem ipsum dolor sit amet, consectetur adipiscing elit, sed do eiusmod tempor incididunt ut labore et dolore magna aliqua. Ut enim ad minim veniam, quis nostrud exercitation ullamco laboris nisi ut aliquip ex ea commodo.</p>
  <span class="btn">View More</span>
  <div class="pager">
    <span><svg width="14" height="14" viewBox="0 0 14 14"><path d="M9 2L4 7l5 5" fill="none" stroke="#999" stroke-width="2"/></svg></span>
    <span class="on"><svg width="14" height="14" viewBox="0 0 14 14"><path d="M5 2l5 5-5 5" fill="none" stroke="#fff" stroke-width="2"/></svg></span>
  </div>
  <div class="project-photos">
    <div role="img" aria-label="Electrician in high-visibility vest at a work site" style="background:linear-gradient(160deg,#b9b1a4,#6b6258)"></div>
    <div role="img" aria-label="Two electricians in hard hats inspecting a panel" style="background:linear-gradient(160deg,#e4c15c,#7c6a4a)"></div>
    <div role="img" aria-label="Workers installing equipment on a site" style="background:linear-gradient(160deg,#d7d1c7,#8a8278)"></div>
  </div>
</section>

<section class="testimonials">
  <div class="label">Client Feedback</div>
  <h2 class="title">What Our Clients Says</h2>
  <div class="avatar" role="img" aria-label="Client portrait" style="left:228px;top:146px;width:56px;height:56px"></div>
  <div class="avatar" role="img" aria-label="Client portrait" style="left:140px;top:280px;width:44px;height:44px"></div>
  <div class="avatar" role="img" aria-label="Client portrait" style="left:350px;top:330px;width:44px;height:44px"></div>
  <div class="avatar" role="img" aria-label="Featured client portrait" style="left:550px;top:110px;width:100px;height:100px"></div>
  <div class="avatar" role="img" aria-label="Client portrait" style="left:820px;top:150px;width:40px;height:40px"></div>
  <div class="avatar" role="img" aria-label="Client portrait" style="left:990px;top:120px;width:56px;height:56px"></div>
  <div class="avatar" role="img" aria-label="Client portrait" style="left:1000px;top:296px;width:40px;height:40px"></div>
  <div class="avatar" role="img" aria-label="Client portrait" style="left:810px;top:330px;width:44px;height:44px"></div>
  <p class="quote">Lorem ipsum dolor sit amet, consectetur adipiscing elit, sed do eiusmod tempor incididunt ut labore et dolore magna aliqua. Ut enim ad minim veniam, quis nostrud exercitation ullamco laboris nisi ut aliquip ex ea commodo consequat.</p>
  <div class="client">Dorian Fells<small>Lorem Ipsum</small></div>
  <div class="dots"><i class="on"></i><i></i><i></i><i></i></div>
</section>

<section class="contact">
  <div class="contact-photo" role="img" aria-label="Smiling electrician in hard hat and safety vest"></div>
  <div class="label">Get In Touch</div>
  <h2 class="title">Contact Us Today</h2>
  <div class="form">
    <div class="field-row"><div class="field">First Name</div><div class="field">Last Name</div></div>
    <div class="field-row"><div class="field">Email Address</div><div class="field">Phone Number</div></div>
    <div class="field-row"><div class="field tall">Message</div></div>
    <span class="btn">Submit Now</span>
  </div>
</section>

<footer class="site-footer">
  <div class="foot-brand"><i></i><b>Brisket &amp; Vane</b>
    <div class="socials"><span></span><span></span><span></span></div>
  </div>
  <div class="col" style="left:400px"><h4>Quick Links</h4>Home<br>About Us<br>Services<br>Projects<br>Contact<br>Schedule A Call</div>
  <div class="col" style="left:584px"><h4>Other Links</h4>Terms of Services<br>Terms &amp; Condition<br>Privacy Policy</div>
  <div class="subscribe">
    <h4>Subscribe for Updates</h4>
    <div class="sub-box"><span>Email Address</span><b></b></div>
    <div class="contact-line"><i></i>Email : info@brisket-vane.example</div>
    <div class="contact-line"><i></i>Phone : +1-555-010-2040</div>
  </div>
  <span class="to-top"></span>
  <div class="copyright">2025 Copyright - Brisket &amp; Vane Electrical Contracting. All Rights Reserved.</div>
</footer>

</body>
</html>
```